Coastline Premier Retreats Business Card Design

Design a business card for Coastline Premier Retreats. Look at the website for colors and reference. Card should have logo, name, title, office number, mobile number, email, URL and a tagline like, "Luxury Hotel & Resort Email Marketing" (This might change).

https://www.coastlinepremierretreats.example

The rest I will leave up to your imagination.

Contact Information for Business Card

Logo, name, title, office number, mobile number, email, URL and a tagline like, "Luxury Hotel & Resort Email Marketing" (This might change).

```html
<!DOCTYPE html>
<html lang="en">
<head>
<meta charset="utf-8">
<title>Coastline Premier Retreats – Business Card</title>
<link rel="stylesheet" href="https://fonts.googleapis.com/css2?family=Montserrat:wght@400;500;700;800&display=swap">
<style>
  :root {
    --backdrop: #2b2b2b;
    --card: #1b1b1b;
    --accent: #f07a16;
    --ink: #ffffff;
    --emboss: #262626;
  }
  * { margin: 0; padding: 0; box-sizing: border-box; }
  html, body {
    width: 1200px; height: 900px; overflow: hidden;
    background: var(--backdrop);
    font-family: "Montserrat", sans-serif;
  }
  .canvas { position: relative; width: 1200px; height: 900px; }

  .card {
    position: absolute;
    width: 560px; height: 320px;
    background: var(--card);
    box-shadow: 0 14px 30px rgba(0,0,0,.55);
  }

  /* Front side */
  .card--front {
    left: 70px; top: 90px;
    border-bottom: 5px solid var(--accent);
    border-left: 3px solid var(--accent);
  }
  .front-mark {
    position: absolute; left: 0; right: 0; top: 96px;
    text-align: center;
    font-weight: 800; font-size: 40px; letter-spacing: 2px;
    text-transform: uppercase;
    color: var(--emboss);
  }
  .tagline {
    position: absolute; left: 0; right: 0; bottom: 52px;
    text-align: center;
    font-size: 17px; font-weight: 500; letter-spacing: .5px;
    color: var(--accent);
  }

  /* Back side */
  .card--back {
    left: 570px; top: 490px;
    border-bottom: 5px solid var(--accent);
    border-left: 3px solid var(--accent);
  }
  .brand {
    position: absolute; left: 34px; top: 104px;
    display: flex; align-items: center; gap: 10px;
  }
  .brand__square { width: 14px; height: 14px; background: var(--accent); }
  .brand__name {
    font-weight: 700; font-size: 15px; letter-spacing: 1px;
    text-transform: uppercase; color: var(--ink);
  }
  .person {
    position: absolute; right: 30px; top: 34px;
    text-align: right;
  }
  .person__name {
    font-weight: 800; font-size: 24px; letter-spacing: 1px;
    text-transform: uppercase; color: var(--accent);
  }
  .person__title { font-size: 14px; color: var(--ink); margin-top: 2px; }
  .person__bar {
    position: absolute; right: -30px; top: 2px;
    width: 14px; height: 34px; background: var(--accent);
  }
  .address {
    position: absolute; left: 60px; top: 170px;
    font-size: 13px; line-height: 1.35; color: var(--ink);
  }
  .contacts {
    position: absolute; left: 34px; top: 218px;
    list-style: none; font-size: 13px; line-height: 1.45; color: var(--ink);
  }
  .contacts li { display: flex; align-items: center; gap: 10px; }
  .contacts svg { width: 14px; height: 14px; fill: var(--accent); flex: none; }
  .contacts .domain { color: var(--accent); }
</style>
</head>
<body>
<main class="canvas">

  <section class="card card--front" aria-label="Card front">
    <p class="front-mark">Coastline Premier Retreats</p>
    <p class="tagline">Luxury Hotel &amp; Resort Email Marketing</p>
  </section>

  <section class="card card--back" aria-label="Card back">
    <div class="brand">
      <span class="brand__square"></span>
      <span class="brand__name">Coastline Premier Retreats</span>
    </div>

    <div class="person">
      <span class="person__bar"></span>
      <p class="person__name">Daniel Mercer</p>
      <p class="person__title">CEO/Founder</p>
    </div>

    <p class="address">Po Box, 48 B Harbor Rd<br>Eastport Bay, NC 27015</p>

    <ul class="contacts">
      <li>
        <svg viewBox="0 0 16 16"><path d="M4 1h8a1 1 0 0 1 1 1v12a1 1 0 0 1-1 1H4a1 1 0 0 1-1-1V2a1 1 0 0 1 1-1zm1 2v9h6V3zm3 10a.8.8 0 1 0 0 1.6A.8.8 0 0 0 8 13z"/></svg>
        555.014.2700
      </li>
      <li>
        <svg viewBox="0 0 16 16"><path d="M1 6c0-2 3-3 7-3s7 1 7 3v1l-3 .5-1-2H5l-1 2L1 7zm3 2h8l1 6H3z"/></svg>
        +34 600 000 147
      </li>
      <li>
        <svg viewBox="0 0 16 16"><path d="M1 4h14v9H1zm1.5 1.2L8 9.2l5.5-4z"/></svg>
        info@coastlinepremierretreats.example
      </li>
      <li>
        <svg viewBox="0 0 16 16"><circle cx="8" cy="8" r="7"/><path d="M1 8h14M8 1c-3 3-3 11 0 14M8 1c3 3 3 11 0 14" stroke="#1b1b1b" stroke-width="1" fill="none"/></svg>
        <span>www.<span class="domain">coastlinepremierretreats</span>.example</span>
      </li>
    </ul>
  </section>

</main>
</body>
</html>
```